Sandwich Board and Poster design promoting a medical aesthetic clinic

I am looking for a clean, modern and relaxing design promoting a medical physician-led aesthetic clinic.
Services offered are neuromodulator treatment (Dyneline) and Dermal Fillers.
Logo must be included.
Use the tag line "Refresh your look, revive your spirit."
Address is 204-205 27361 93 Ave, Surrey, K7P 2R4
604-555-0172
email - info@brightmoorskin.ca
www.brightmoorskin.ca

```html
<!DOCTYPE html>
<html lang="en">
<head>
<meta charset="utf-8">
<title>Brightmoor Skin – Poster</title>
<link rel="stylesheet" href="https://fonts.googleapis.com/css2?family=Montserrat:wght@500&family=Poppins:wght@400;700&family=Gilda+Display&family=Mrs+Saint+Delafield&family=Allura&display=swap">
<style>
  :root{
    --navy:#0c1a34;
    --navy-deep:#08142a;
    --indigo:#2b2a6b;
    --gold:#d9b02a;
    --gold-deep:#b8901c;
    --ink:#0f2540;
    --white:#ffffff;
    --mist:#eef4f6;
  }
  *{margin:0;padding:0;box-sizing:border-box}
  html,body{width:940px;height:1200px;overflow:hidden;background:#bdbdbd}
  .poster{position:relative;width:940px;height:1200px;overflow:hidden;background:var(--mist)}
  .hero-photo{position:absolute;inset:0;
    background:
      radial-gradient(ellipse 420px 260px at 560px 640px,#c89672 0%,rgba(200,150,114,0) 70%),
      radial-gradient(ellipse 380px 240px at 220px 720px,#c08b66 0%,rgba(192,139,102,0) 75%),
      radial-gradient(ellipse 160px 200px at 760px 640px,#f2f2f2 0%,rgba(242,242,242,0) 75%),
      linear-gradient(180deg,#e9f2f5 0%,#f4f8f9 40%,#e6e1da 58%,#cfa482 80%,#b9825e 100%)}
  .leaves{position:absolute;top:0;width:300px;height:360px}
  .leaves--left{left:0;background:radial-gradient(ellipse 200px 180px at 40px 60px,#3f9a24 0%,#6cbc3a 45%,rgba(108,188,58,0) 100%)}
  .leaves--right{right:0;background:radial-gradient(ellipse 260px 240px at 260px 80px,#2f8a1e 0%,#6cbc3a 50%,rgba(108,188,58,0) 100%)}

  .brand{position:absolute;left:0;width:940px;top:200px;text-align:center;font-family:"Montserrat",sans-serif;font-weight:500;color:var(--ink)}
  .brand__mark{display:block;width:14px;height:14px;border-radius:50%;background:var(--gold);margin:0 auto 14px}
  .brand__name{font-size:36px;letter-spacing:14px;padding-left:14px;line-height:1}
  .brand__sub{font-size:12px;letter-spacing:8px;padding-left:8px;margin-top:10px}

  .tagline{position:absolute;left:62px;top:262px}
  .tagline__script{font-family:"Mrs Saint Delafield",cursive;font-size:112px;color:var(--ink);line-height:1}
  .tagline__gold{position:absolute;left:0;top:80px;white-space:nowrap;font-family:"Gilda Display",serif;font-size:68px;color:var(--gold);line-height:1}
  .tagline__revive{position:absolute;left:0;top:145px;white-space:nowrap;font-family:"Gilda Display",serif;font-size:43px;color:var(--ink);line-height:1}

  .divider{position:absolute;left:546px;top:289px;width:2px;height:156px;background:var(--gold)}
  .services__title{position:absolute;left:562px;top:280px;font-family:"Allura",cursive;font-size:44px;color:var(--ink);line-height:1}
  .service{position:absolute;left:563px;width:246px;background:var(--indigo);border-radius:4px;color:var(--white);font-family:"Poppins",sans-serif;font-size:18px;line-height:1.05;padding:0 10px 0 30px;display:flex;align-items:center}
  .service svg{position:absolute;left:8px;top:50%;margin-top:-8px}
  .service--one{top:346px;height:52px}
  .service--two{top:402px;height:50px}

  .base{position:absolute;left:0;top:0}
  .snap{position:absolute;border-radius:50%;border:4px solid var(--gold)}
  .snap--brow{left:320px;top:905px;width:162px;height:162px;background:radial-gradient(circle at 60% 40%,#c89472,#8a5b3f 70%,#5b6fb0)}
  .snap--eyes{left:486px;top:875px;width:172px;height:172px;background:radial-gradient(circle at 40% 65%,#b7805c,#6e4630 60%,#3a4fa8)}
  .snap--lips{left:662px;top:806px;width:210px;height:210px;background:radial-gradient(circle at 55% 45%,#f1d6cb,#dfb4a6 55%,#4a5fc8)}

  .contact__title{position:absolute;left:64px;top:990px;font-family:"Allura",cursive;font-size:66px;color:var(--white);line-height:1}
  .contact__line{position:absolute;display:flex;align-items:center;gap:10px;font-family:"Poppins",sans-serif;color:var(--white)}
  .contact__line svg{flex:none}
  .contact__phone{left:62px;top:1083px;font-size:24px;font-weight:700}
  .contact__email{left:62px;top:1124px;font-size:19px}
  .contact__address{left:386px;top:1085px;font-size:20px}
  .web{position:absolute;left:368px;top:1117px;width:508px;height:28px;border-radius:14px;background:var(--gold);display:flex;align-items:center;justify-content:center;gap:8px;color:var(--navy)}
  .web__lead{font-family:"Allura",cursive;font-size:24px}
  .web__url{font-family:"Poppins",sans-serif;font-size:19px;letter-spacing:5px}
  .web__url b{font-weight:700}
</style>
</head>
<body>
<main class="poster">
  <div class="hero-photo" role="img" aria-label="Spa photo: a client lying back with a towel headband receiving a facial injection, lilies and an oil bottle behind"></div>
  <div class="leaves leaves--left" role="img" aria-label="Tropical leaves"></div>
  <div class="leaves leaves--right" role="img" aria-label="Palm leaves"></div>

  <header class="brand">
    <span class="brand__mark"></span>
    <div class="brand__name">BRIGHTMOOR</div>
    <div class="brand__sub">SKIN</div>
  </header>

  <section class="tagline">
    <div class="tagline__script">Refresh</div>
    <div class="tagline__gold">Your Look</div>
    <div class="tagline__revive">Revive Your Spirit</div>
  </section>

  <div class="divider"></div>
  <section class="services">
    <div class="services__title">Services offered</div>
    <div class="service service--one">
      <svg width="16" height="16" viewBox="0 0 16 16"><circle cx="8" cy="8" r="6" fill="none" stroke="#d9b02a" stroke-width="1.2"/><circle cx="8" cy="8" r="2" fill="#d9b02a"/></svg>
      Neuromodulator Treatment (Dyneline)
    </div>
    <div class="service service--two">
      <svg width="16" height="16" viewBox="0 0 16 16"><circle cx="8" cy="8" r="6" fill="none" stroke="#d9b02a" stroke-width="1.2"/><circle cx="8" cy="8" r="2" fill="#d9b02a"/></svg>
      Dermal Fillers
    </div>
  </section>

  <svg class="base" width="940" height="1200" viewBox="0 0 940 1200">
    <path d="M0 860 C200 925 420 925 600 865 C740 820 860 760 940 700 L940 1200 L0 1200 Z" fill="#0c1a34"/>
    <path d="M0 852 C200 918 420 918 600 858 C740 812 860 752 940 690 L940 705 C860 768 740 828 600 874 C420 934 200 934 0 870 Z" fill="#d9b02a"/>
    <path d="M0 890 C220 950 430 945 610 890 C740 850 860 790 940 740 L940 748 C860 798 740 858 610 898 C430 953 220 958 0 898 Z" fill="#b8901c"/>
  </svg>

  <div class="snap snap--brow" role="img" aria-label="Close-up photo of a forehead injection"></div>
  <div class="snap snap--eyes" role="img" aria-label="Close-up photo of a gloved hand treating the brow area"></div>
  <div class="snap snap--lips" role="img" aria-label="Close-up photo of lip filler result"></div>

  <section class="contact">
    <div class="contact__title">Contact Us</div>
    <div class="contact__line contact__phone">
      <svg width="18" height="18" viewBox="0 0 18 18"><circle cx="9" cy="9" r="9" fill="#d9b02a"/><path d="M6 5l2 2-1 1.2c.6 1.2 1.5 2.1 2.8 2.8L11 10l2 2-1.2 1.3C8.5 13 5 9.5 4.7 6.2Z" fill="#0c1a34"/></svg>
      604-555-0172
    </div>
    <div class="contact__line contact__email">
      <svg width="18" height="18" viewBox="0 0 18 18"><circle cx="9" cy="9" r="9" fill="#d9b02a"/><rect x="4.5" y="6" width="9" height="6.5" fill="none" stroke="#0c1a34" stroke-width="1.2"/><path d="M4.5 6l4.5 3.5L13.5 6" fill="none" stroke="#0c1a34" stroke-width="1.2"/></svg>
      info@brightmoorskin.ca
    </div>
    <div class="contact__line contact__address">
      <svg width="18" height="20" viewBox="0 0 18 20"><path d="M9 1C5 1 2 4 2 7.8 2 12.5 9 19 9 19s7-6.5 7-11.2C16 4 13 1 9 1Z" fill="#d9b02a"/><circle cx="9" cy="8" r="2.6" fill="#0c1a34"/></svg>
      204-205 27361 93 Ave, Surrey, K7P 2R4
    </div>
    <div class="web">
      <span class="web__lead">Visit us on</span>
      <span class="web__url">www.<b>brightmoorskin</b>.ca</span>
    </div>
  </section>
</main>
</body>
</html>
```